Change of trading name, rebrand

existing website to be updated with new theme and logo. existing website is
www.harlowbrentmere.com.au
Industry/Entity Type
Construction
Coding
Coded - Design and coding required
Number of Pages Required
5+ page
Requirements
Must have
- be mobile phone friendly

```html
<!DOCTYPE html>
<html lang="en">
<head>
<meta charset="utf-8">
<title>HBM Plant Hire</title>
<meta name="viewport" content="width=1200">
<link href="https://fonts.googleapis.com/css2?family=Krona+One&family=Roboto:wght@400;500;700&display=swap" rel="stylesheet">
<style>
:root{
  --navy:#2a2c85;
  --navy-dark:#1f2068;
  --ink:#111111;
  --text:#555555;
  --muted:#d4d4d4;
  --panel:#f4f4f4;
  --white:#ffffff;
}
*{box-sizing:border-box;margin:0;padding:0}
html,body{width:1200px;height:4108px;overflow:hidden}
body{position:relative;font-family:'Roboto',sans-serif;color:var(--ink);background:var(--white)}
.abs{position:absolute}
.display{font-family:'Krona One',sans-serif;letter-spacing:1px}
.btn{position:absolute;display:flex;align-items:center;justify-content:center;background:var(--navy);color:var(--white);font-weight:700;font-size:14px;text-transform:uppercase}

/* header */
.topbar{left:0;top:0;width:1200px;height:89px;background:var(--white)}
.navbar{left:0;top:89px;width:1200px;height:48px;background:var(--ink)}
.brand{left:38px;top:0;width:220px;height:137px;background:var(--white);display:flex;align-items:center;justify-content:center;gap:8px;box-shadow:0 2px 6px rgba(0,0,0,.15)}
.brand-mark{width:14px;height:14px;background:var(--navy)}
.brand-name{font-weight:700;font-size:20px;color:var(--navy);line-height:1.1}
.nav a{position:absolute;top:105px;font-size:12px;font-weight:700;color:var(--white);text-decoration:none}
.nav a.active{border-bottom:2px solid var(--white);padding-bottom:3px}
.social{position:absolute;width:38px;height:38px;border:1px solid #ddd;display:flex;align-items:center;justify-content:center;background:var(--white)}
.social i{width:10px;height:10px;border-radius:50%;background:var(--ink)}
.social.on{background:var(--navy);border-color:var(--navy)}
.social.on i{background:var(--white)}
.quote{left:788px;top:21px;width:147px;height:46px;border:2px solid var(--navy);color:var(--navy);font-weight:700;font-size:14px;display:flex;align-items:center;justify-content:center;background:var(--white)}
.callbox{left:0;top:0}
.call-label{left:1080px;top:42px;font-size:11px;font-weight:700;color:var(--white)}
.call-num{left:1006px;top:80px;font-size:26px;font-weight:700;color:var(--white)}
.call-icon{left:1026px;top:32px;width:38px;height:38px;border-radius:50%;background:var(--white);display:flex;align-items:center;justify-content:center}

/* hero */
.hero{left:0;top:137px;width:1200px;height:663px;background:linear-gradient(180deg,#8fb6de 0%,#c9d9e6 35%,#a29a8a 60%,#7b7266 100%)}
.hero-title{left:0;top:325px;width:1200px;text-align:center;font-size:42px;color:var(--white);text-shadow:0 2px 6px rgba(0,0,0,.4)}
.hero-sub{left:0;top:383px;width:1200px;text-align:center;font-size:23px;color:var(--white);text-shadow:0 2px 6px rgba(0,0,0,.5)}
.dot{position:absolute;left:1149px;width:12px;height:12px;border-radius:50%;border:1.5px solid var(--white)}
.dot.on{background:var(--white)}

.section-title{position:absolute;left:0;width:1200px;text-align:center;font-size:36px;line-height:48px;color:var(--ink)}
.section-title .soft{color:var(--muted)}
.rule{position:absolute;left:563px;width:74px;height:4px;background:var(--navy)}

/* about */
.about-frame{left:112px;top:870px;width:333px;height:514px;border:2px solid var(--navy)}
.about-photo{left:121px;top:881px;width:315px;height:493px;background:linear-gradient(180deg,#4f86c9 0%,#9ab6cf 40%,#7a7a72 70%,#9a968c 100%)}
.about-inset{left:346px;top:1088px;width:206px;height:253px;border:8px solid var(--white);background:linear-gradient(180deg,#7ea6d4 0%,#c3a57b 60%,#a68355 100%)}
.about-head{left:600px;top:902px;width:480px;font-size:22px;font-weight:700;line-height:32px}
.about-copy{left:600px;top:985px;width:489px;font-size:13px;line-height:23px;color:var(--text);text-align:justify}
.about-copy p+p{margin-top:12px}

/* plant cards */
.card-photo{position:absolute;width:303px;height:240px}
.card-label{position:absolute;width:266px;height:77px;background:var(--white);box-shadow:0 3px 8px rgba(0,0,0,.12);display:flex;align-items:center;padding-left:25px;font-size:14px;font-weight:700;line-height:24px;text-transform:uppercase}
.card-label.active{background:var(--navy);color:var(--white)}
.card-top{position:absolute;height:8px;background:var(--navy)}

/* stats */
.stats{left:0;top:2435px;width:1200px;height:273px;background:linear-gradient(90deg,#25277a,#2e3190 50%,#25277a)}
.stat{position:absolute;top:2495px;width:200px;text-align:center;color:var(--white)}
.stat svg{display:block;margin:0 auto 12px}
.stat h4{font-size:18px;font-weight:500;line-height:26px;text-transform:uppercase}
.stat strong{display:block;font-size:36px;font-weight:700;margin-top:8px}
.stat-div{position:absolute;top:2508px;width:1px;height:130px;background:rgba(255,255,255,.25)}

/* partners */
.partner{position:absolute;top:2914px;width:171px;height:93px;background:var(--white);box-shadow:0 3px 10px rgba(0,0,0,.12);display:flex;align-items:center;justify-content:center}
.partner i{display:block;width:96px;height:26px;border-radius:13px;background:#dcdcdc}

/* contact */
.contact-photo{left:0;top:3117px;width:600px;height:566px;background:linear-gradient(180deg,#5d93d4 0%,#b8cde0 40%,#b0a99a 65%,#c9c2b4 100%)}
.contact-panel{left:600px;top:3117px;width:600px;height:566px;background:var(--panel)}
.field-label{position:absolute;font-size:13px;color:#444}
.field{position:absolute;height:43px;background:var(--white);border:1px solid #e6e6e6}

/* footer */
.footer{left:0;top:3683px;width:1200px;height:425px;background:#121212}
.foot-brand{left:0;top:3740px;width:1200px;display:flex;align-items:center;justify-content:center;gap:10px}
.foot-brand .brand-mark{background:var(--white)}
.foot-brand .brand-name{color:var(--white);font-size:24px}
.foot-line{position:absolute;left:112px;width:976px;height:1px;background:#333}
.foot-nav a{position:absolute;top:3866px;font-size:15px;font-weight:700;color:var(--white);text-decoration:none}
.foot-icon{position:absolute;top:3934px;width:75px;height:74px;background:var(--white);display:flex;align-items:center;justify-content:center}
.foot-info{position:absolute;top:3950px;font-size:13px;color:var(--white);line-height:24px}
.foot-info b{font-weight:500}
.foot-div{position:absolute;top:3934px;width:1px;height:74px;background:#333}
.copy{left:0;top:4068px;width:1200px;text-align:center;font-size:12px;color:var(--white)}
.fsocial{position:absolute;top:4058px;width:37px;height:37px;background:var(--white);display:flex;align-items:center;justify-content:center}
.fsocial i{width:10px;height:10px;border-radius:50%;background:var(--ink)}
.fsocial.on{background:var(--navy)}
.fsocial.on i{background:var(--white)}
</style>
</head>
<body>

<!-- Header -->
<div class="abs topbar"></div>
<div class="abs navbar"></div>
<svg class="abs callbox" width="1200" height="137" viewBox="0 0 1200 137" aria-hidden="true">
  <polygon points="990,0 1200,0 1200,137 935,137 990,90" fill="var(--navy)"/>
</svg>
<div class="abs brand"><span class="brand-mark"></span><span class="brand-name">HBM PLANT HIRE</span></div>
<nav class="nav">
  <a class="active" style="left:289px">HOME</a>
  <a style="left:354px">ABOUT US</a>
  <a style="left:445px">PLANT HIRE ▾</a>
  <a style="left:559px">MAJOR PROJECT</a>
  <a style="left:691px">POLICIES</a>
  <a style="left:775px">JOBS</a>
  <a style="left:836px">CONTACT US</a>
</nav>
<a class="social on" style="left:630px;top:26px" aria-label="Social profile"><i></i></a>
<a class="social" style="left:675px;top:26px" aria-label="Social profile"><i></i></a>
<a class="social" style="left:720px;top:26px" aria-label="Social profile"><i></i></a>
<a class="abs quote">GET A QUOTE</a>
<div class="abs call-icon">
  <svg width="18" height="18" viewBox="0 0 24 24"><path d="M6.6 10.8a15 15 0 0 0 6.6 6.6l2.2-2.2c.3-.3.7-.4 1-.2 1.1.4 2.3.6 3.6.6.6 0 1 .4 1 1V20c0 .6-.4 1-1 1A17 17 0 0 1 3 4c0-.6.4-1 1-1h3.5c.6 0 1 .4 1 1 0 1.3.2 2.5.6 3.6.1.3 0 .7-.2 1z" fill="var(--navy)"/></svg>
</div>
<div class="abs call-label">CALL US TODAY!</div>
<div class="abs call-num">1300 555 214</div>

<!-- Hero -->
<div class="abs hero" role="img" aria-label="Orange excavator digging on an earthworks site under a blue sky"></div>
<svg class="abs" style="left:0;top:600px" width="1200" height="200" viewBox="0 0 1200 200" aria-hidden="true">
  <polygon points="0,118 600,10 0,163" fill="#dcdcdc"/>
  <polygon points="600,10 1200,120 1200,200 0,200 0,163" fill="var(--white)"/>
  <polygon points="600,10 1200,110 1200,187" fill="var(--navy)"/>
</svg>
<h1 class="abs hero-title display">HBM PLANT HIRE</h1>
<p class="abs hero-sub">Committed to superior quality plant hire services.</p>
<a class="btn" style="left:527px;top:439px;width:145px;height:45px">GET STARTED</a>
<span class="dot" style="top:588px"></span>
<span class="dot on" style="top:610px"></span>
<span class="dot" style="top:633px"></span>
<span class="dot" style="top:655px"></span>

<!-- About -->
<h2 class="section-title display" style="top:728px">HBM HEAVY<br><span class="soft">EQUIPMENT HIRE</span></h2>
<div class="rule" style="top:828px"></div>
<div class="abs about-frame"></div>
<div class="abs about-photo" role="img" aria-label="Yellow backhoe loader parked on a work site"></div>
<div class="abs about-inset" role="img" aria-label="Excavator working in a trench"></div>
<h3 class="abs about-head">COMMITTED TO SUPERIOR QUALITY<br>PLANT HIRE SERVICES.</h3>
<div class="abs about-copy">
  <p>Harlow Brentmere Heavy Equipment Hire specialise in the hire of heavy earthmoving, mining and construction machines with specialised attachments and tooling. Our array of machines and attachments is second to none, and we have one of the largest hire fleets available in South East Queensland. If its plant hire you require, then Harlow Brentmere Resources, or HBM as the local's call us – should be the first call you make. Wet or dry hire, we provide excellent operators and quality machines across all makes and models to guarantee you maximum up-time.</p>
  <p>We employ a group of highly skilled and capable managers who have worked throughout construction sites in Queensland, NSW and other parts of Australia to deliver a vast array of plant and equipment to mining, civil, building and industrial projects.</p>
</div>
<a class="btn" style="left:600px;top:1302px;width:147px;height:47px">LEARN MORE</a>

<!-- Plant hire -->
<h2 class="section-title display" style="top:1561px">PLANT <span class="soft">HIRE</span></h2>
<div class="rule" style="top:1612px"></div>

<div class="card-photo" style="left:112px;top:1658px;background:linear-gradient(180deg,#a9c4e2,#d8dde3 45%,#7d7d7d)" role="img" aria-label="Wheeled excavator"></div>
<div class="card-top" style="left:449px;top:1658px;width:303px"></div>
<div class="card-photo" style="left:449px;top:1666px;height:232px;background:linear-gradient(180deg,#6c9ad1,#c9b35a 55%,#8a8a88)" role="img" aria-label="Tracked bulldozer"></div>
<div class="card-photo" style="left:785px;top:1658px;background:linear-gradient(180deg,#5c8fd0,#d5c056 55%,#9a9484)" role="img" aria-label="Swamp dozer"></div>
<div class="card-label" style="left:112px;top:1859px">EXCAVATORS &amp; DIGGERS<br>FOR HIRE</div>
<div class="card-label active" style="left:449px;top:1859px">DOZERS FOR HIRE</div>
<div class="card-label" style="left:785px;top:1859px">SWAMP DOZERS FOR HIRE</div>

<div class="card-photo" style="left:112px;top:1976px;background:linear-gradient(180deg,#8fb0d6,#c9b953 50%,#6a6656)" role="img" aria-label="Articulated dump truck"></div>
<div class="card-photo" style="left:449px;top:1976px;background:linear-gradient(180deg,#b2c8e0,#c6ab5a 55%,#7c7a74)" role="img" aria-label="Motor grader"></div>
<div class="card-photo" style="left:785px;top:1976px;background:linear-gradient(180deg,#9fbde0,#5a5a5e 55%,#b0754a)" role="img" aria-label="Wheel loader beside stacked pipes"></div>
<div class="card-label" style="left:112px;top:2177px">ARTICULATED, TRACKED &amp;<br>RIGID DUMP TRUCKS FOR HIRE</div>
<div class="card-label" style="left:449px;top:2177px">GRADERS FOR HIRE</div>
<div class="card-label" style="left:785px;top:2177px">LOADERS FOR HIRE</div>
<a class="btn" style="left:540px;top:2303px;width:120px;height:48px">VIEW ALL</a>

<!-- Stats -->
<div class="abs stats"></div>
<div class="stat" style="left:85px">
  <svg width="46" height="44" viewBox="0 0 46 44"><circle cx="23" cy="14" r="10" fill="none" stroke="#fff" stroke-width="4" stroke-dasharray="4 3"/><circle cx="23" cy="14" r="4" fill="#fff"/><rect x="8" y="26" width="30" height="16" rx="6" fill="#fff"/></svg>
  <h4>YEARS<br>OF EXPERIENCE</h4><strong>20+</strong>
</div>
<div class="stat-div" style="left:290px"></div>
<div class="stat" style="left:294px">
  <svg width="46" height="44" viewBox="0 0 46 44"><rect x="4" y="24" width="24" height="14" rx="2" fill="#fff"/><circle cx="10" cy="40" r="3" fill="#fff"/><circle cx="22" cy="40" r="3" fill="#fff"/><path d="M28 26 L38 6 L44 14 L36 22" fill="none" stroke="#fff" stroke-width="4"/><rect x="8" y="14" width="12" height="9" fill="#fff"/></svg>
  <h4>MACHINES IN<br>FLEET</h4><strong>100+</strong>
</div>
<div class="stat-div" style="left:499px"></div>
<div class="stat" style="left:502px">
  <svg width="46" height="44" viewBox="0 0 46 44"><path d="M4 24 L16 14 L26 18 L34 12 L44 22 L30 34 L20 30 L10 34 Z" fill="#fff"/><path d="M18 6 L23 2 L28 6" fill="none" stroke="#fff" stroke-width="3"/></svg>
  <h4>ONE OF QLD'S<br>LARGEST<br>SUPPLIERS</h4>
</div>
<div class="stat-div" style="left:708px"></div>
<div class="stat" style="left:711px">
  <svg width="46" height="44" viewBox="0 0 46 44"><circle cx="23" cy="22" r="14" fill="none" stroke="#fff" stroke-width="6" stroke-dasharray="6 4"/><circle cx="23" cy="22" r="7" fill="none" stroke="#fff" stroke-width="4"/></svg>
  <h4>ONSITE<br>SERVICING</h4>
</div>
<div class="stat-div" style="left:917px"></div>
<div class="stat" style="left:920px">
  <svg width="46" height="44" viewBox="0 0 46 44"><path d="M10 4 H34 V16 H22 V26 H34 V40 H12 V30 H18 V34 H28 V30 H16 V10 H10 Z" fill="#fff"/></svg>
  <h4>CUSTOM MACHINE<br>ATTACHMENTS</h4>
</div>

<!-- Partners -->
<h2 class="section-title display" style="top:2813px">OUR <span class="soft">PARTNERS</span></h2>
<div class="rule" style="top:2864px"></div>
<svg class="abs" style="left:50px;top:2948px" width="18" height="26" viewBox="0 0 18 26"><path d="M14 3 L4 13 L14 23" fill="none" stroke="#999" stroke-width="2.5"/></svg>
<div class="partner" style="left:112px" aria-label="Partner badge"><i></i></div>
<div class="partner" style="left:313px" aria-label="Partner badge"><i></i></div>
<div class="partner" style="left:514px" aria-label="Partner badge"><i></i></div>
<div class="partner" style="left:715px" aria-label="Partner badge"><i></i></div>
<div class="partner" style="left:916px" aria-label="Partner badge"><i></i></div>
<svg class="abs" style="left:1132px;top:2948px" width="18" height="26" viewBox="0 0 18 26"><path d="M4 3 L14 13 L4 23" fill="none" stroke="var(--navy)" stroke-width="3"/></svg>

<!-- Contact -->
<div class="abs contact-photo" role="img" aria-label="Orange wheeled excavator parked in a yard"></div>
<div class="abs contact-panel"></div>
<h2 class="abs display" style="left:672px;top:3190px;font-size:36px">CONTACT <span style="color:var(--muted)">US</span></h2>
<div class="abs" style="left:672px;top:3238px;width:74px;height:4px;background:var(--navy)"></div>
<span class="field-label" style="left:672px;top:3270px">First Name</span>
<span class="field-label" style="left:905px;top:3270px">Last Name</span>
<div class="field" style="left:672px;top:3299px;width:223px"></div>
<div class="field" style="left:905px;top:3299px;width:223px"></div>
<span class="field-label" style="left:672px;top:3356px">Phone</span>
<span class="field-label" style="left:905px;top:3356px">Email</span>
<div class="field" style="left:672px;top:3385px;width:223px"></div>
<div class="field" style="left:905px;top:3385px;width:223px"></div>
<span class="field-label" style="left:672px;top:3442px">Enquiry</span>
<div class="field" style="left:672px;top:3471px;width:456px;height:69px"></div>
<a class="btn" style="left:956px;top:3556px;width:171px;height:46px">SEND MESSAGE</a>

<!-- Footer -->
<div class="abs footer"></div>
<div class="abs foot-brand"><span class="brand-mark"></span><span class="brand-name">HBM PLANT HIRE</span></div>
<div class="foot-line" style="top:3845px"></div>
<div class="foot-line" style="top:3905px"></div>
<nav class="foot-nav">
  <a style="left:193px">HOME</a>
  <a style="left:280px">ABOUT US</a>
  <a style="left:400px">PLANT HIRE</a>
  <a style="left:535px">MAJOR PROJECT</a>
  <a style="left:710px">POLICIES</a>
  <a style="left:822px">JOBS</a>
  <a style="left:904px">CONTACT US</a>
</nav>
<div class="foot-icon" style="left:112px">
  <svg width="30" height="34" viewBox="0 0 24 28"><path d="M12 2a8 8 0 0 0-8 8c0 6 8 14 8 14s8-8 8-14a8 8 0 0 0-8-8z" fill="none" stroke="var(--navy)" stroke-width="2.5"/><circle cx="12" cy="10" r="3" fill="var(--navy)"/><ellipse cx="12" cy="25" rx="7" ry="2" fill="none" stroke="var(--navy)" stroke-width="1.5"/></svg>
</div>
<div class="foot-info" style="left:211px"><b>LOCATION:</b><br>18 Kestrel Rd, Marlowe QLD 4210</div>
<div class="foot-div" style="left:440px"></div>
<div class="foot-icon" style="left:504px">
  <svg width="32" height="32" viewBox="0 0 24 24"><path d="M6.6 10.8a15 15 0 0 0 6.6 6.6l2.2-2.2c.3-.3.7-.4 1-.2 1.1.4 2.3.6 3.6.6.6 0 1 .4 1 1V20c0 .6-.4 1-1 1A17 17 0 0 1 3 4c0-.6.4-1 1-1h3.5c.6 0 1 .4 1 1 0 1.3.2 2.5.6 3.6.1.3 0 .7-.2 1z" fill="var(--navy)"/></svg>
</div>
<div class="foot-info" style="left:603px"><b>PHONE:</b><br>1300 555 214</div>
<div class="foot-div" style="left:776px"></div>
<div class="foot-icon" style="left:855px">
  <svg width="32" height="32" viewBox="0 0 24 24"><rect x="3" y="7" width="18" height="14" rx="2" fill="var(--navy)"/><rect x="7" y="3" width="10" height="6" fill="none" stroke="var(--navy)" stroke-width="2"/><rect x="12" y="11" width="6" height="2" fill="#fff"/><rect x="12" y="15" width="6" height="2" fill="#fff"/></svg>
</div>
<div class="foot-info" style="left:954px"><b>FAX:</b><br>07 3000 1842</div>
<div class="foot-line" style="top:4045px"></div>
<p class="abs copy">© 2024 HBM PLANT HIRE &nbsp;|&nbsp; All Rights Reserved</p>
<a class="fsocial on" style="left:957px" aria-label="Social profile"><i></i></a>
<a class="fsocial" style="left:1004px" aria-label="Social profile"><i></i></a>
<a class="fsocial" style="left:1051px" aria-label="Social profile"><i></i></a>

</body>
</html>
```